Website for a company offering full serivce charging solutions for electric cars

The company "tanu-werk" (english: "tanu-works") offering all-in-one-solutions for charging infrastructure for electric mobility.

There are four products:
1- Wallboxes for single-family homes
2- Solutions for property devloper/-management for property parking space
3- All-in-one-charging solution for municipalities/communities
4- Solutions for tourism/hotels/holiday appartments

The Website structure:
1. Main Page
2.1. Product Page Single Homes
2.2. Product Page Property Management / Parking
2.3. Product Page Municipality
2.4. Product Page Tourism
3. Contact Form / Request for information
4. Imprint / Legal

The Website should be built on Wordpress with a powerful possibility to simply add/modify specific landing pages.

We would like you to implement the website later and also maintain it if possible, but we would be able to do minor modifications by ourselfs (for A/B-Testing)

The website should be clear and simple, easy to understand.
Target group is mainly B2C without deeper knowledge of that topic.

It should suggest, that we will provide a very simple way to get the charging infrastructure done.

We need a contact form, maybe we will use Hubspot later.

Attached you will find a draft of the main page and a landing page (for 2.2) - it is just the content, please ignore the design. We would love to let you create a suitable design.
Also you will find some drafts a bit different for the same story.

I added also a few stock photos, but they don't need to be used! If you have better ideas, you are welcome!

Industry/Entity Type

Charging/Electric mobility

Number of Pages Required

2 page

Font styles to use
Sans Serif

Requirements
Must have
• Based on Wordpress, and the designer should be able to implement it on Wordpress on a later step

```html
<!DOCTYPE html>
<html lang="de">
<head>
<meta charset="utf-8">
<title>tanu-werk – Lösungen</title>
<link rel="stylesheet" href="https://fonts.googleapis.com/css2?family=Audiowide&family=Poppins:wght@400;500;600&display=swap">
<style>
  :root {
    --ink: #141824;
    --text: #2b2f3a;
    --pink: #e6198a;
    --purple: #9b45c9;
    --night: #111827;
    --white: #ffffff;
    --lilac: #efe6f7;
  }
  * { box-sizing: border-box; margin: 0; padding: 0; }
  html, body { width: 1200px; height: 2162px; overflow: hidden; }
  body {
    position: relative;
    background: var(--white);
    font-family: "Poppins", sans-serif;
    color: var(--text);
  }
  .backdrop { position: absolute; inset: 0; width: 1200px; height: 2162px; }

  .brand { display: flex; align-items: center; gap: 10px; font-family: "Poppins", sans-serif; font-weight: 500; }
  .brand-dot { width: 22px; height: 22px; border-radius: 50%; background: var(--pink); }

  .site-header { position: absolute; left: 89px; top: 22px; width: 1022px; height: 44px; display: flex; align-items: center; justify-content: space-between; }
  .site-header .brand { font-size: 28px; color: var(--ink); }
  .main-nav { display: flex; align-items: center; gap: 30px; font-size: 14.5px; color: var(--ink); }
  .main-nav .active { color: var(--pink); }
  .btn-contact { border: 2px solid var(--purple); border-radius: 22px; padding: 9px 26px; font-weight: 600; font-size: 12.5px; letter-spacing: .5px; }

  h1, h2 { font-family: "Audiowide", sans-serif; font-weight: 400; color: var(--ink); line-height: 1.0; }

  .hero { position: absolute; left: 88px; top: 234px; width: 560px; }
  .hero h1 { font-size: 31px; margin-bottom: 12px; }
  .hero .lead { font-size: 15.5px; line-height: 24px; font-weight: 500; }
  .hero .lead + .lead { margin-top: 6px; }
  .hero .note { font-size: 14px; margin-top: 14px; }

  .checks { list-style: none; }
  .checks li { position: relative; padding-left: 22px; }
  .checks li::before {
    content: ""; position: absolute; left: 0; top: 5px; width: 11px; height: 11px; border-radius: 50%; background: var(--pink);
  }
  .checks li::after {
    content: ""; position: absolute; left: 3.5px; top: 7.5px; width: 3px; height: 5px;
    border: solid var(--white); border-width: 0 1.6px 1.6px 0; transform: rotate(45deg);
  }
  .hero .checks { margin-top: 10px; font-size: 14px; line-height: 22.3px; }
  .hero .checks li::before { top: 5.5px; }
  .hero .checks li::after { top: 8px; }

  .deco-ring { position: absolute; left: 634px; top: 330px; width: 320px; height: 320px; border-radius: 50%;
    background: linear-gradient(135deg, var(--pink), var(--purple)); }
  .photo { position: absolute; border-radius: 16px; box-shadow: 0 24px 40px rgba(20,24,36,.12); }
  .photo-socket { left: 676px; top: 130px; width: 434px; height: 463px;
    background: radial-gradient(circle at 50% 50%, #3a3d42 0%, #1e2024 45%, #5a6068 100%); }
  .photo-charging { left: 87px; top: 875px; width: 448px; height: 670px;
    background: linear-gradient(160deg, #d5d9de 0%, #a9b0b8 40%, #555c64 75%, #2d3136 100%); }

  .service { position: absolute; left: 600px; top: 934px; width: 512px; }
  .service h2 { font-size: 31px; margin-bottom: 8px; }
  .service .intro { font-size: 14.5px; line-height: 22.3px; color: var(--ink); }
  .service .checks { margin-top: 18px; font-size: 14.5px; line-height: 22.3px; }
  .service .checks li { padding-left: 27px; margin-bottom: 7px; }
  .service .checks li:nth-child(n+6) { margin-bottom: 4px; }

  .site-footer { position: absolute; left: 0; top: 1890px; width: 1200px; text-align: center; color: var(--white); }
  .site-footer .brand { justify-content: center; font-size: 31px; color: var(--white); }
  .footer-links { display: flex; justify-content: center; gap: 23px; margin-top: 26px; font-size: 16px; }
  .socials { display: flex; justify-content: center; gap: 9px; margin-top: 24px; }
  .social { width: 42px; height: 42px; border-radius: 50%; background: #1f2633; display: flex; align-items: center; justify-content: center; }
  .social span { width: 12px; height: 12px; border-radius: 50%; background: var(--white); }
  .footer-rule { position: absolute; left: 89px; top: 2111px; width: 1022px; height: 1px; background: #2e3645; }
  .copyright { position: absolute; left: 0; top: 2126px; width: 1200px; text-align: center; font-size: 14.5px; color: var(--white); }
  .to-top { position: absolute; left: 1130px; top: 2094px; width: 34px; height: 34px; border-radius: 50%;
    background: linear-gradient(135deg, var(--pink), var(--purple)); }
  .to-top::after { content: ""; position: absolute; left: 14px; top: 15px; width: 5px; height: 5px;
    border: solid var(--white); border-width: 1.5px 0 0 1.5px; transform: rotate(45deg); }
</style>
</head>
<body>
  <svg class="backdrop" viewBox="0 0 1200 2162" aria-hidden="true">
    <defs>
      <linearGradient id="softWave" x1="0" y1="0" x2="0" y2="1">
        <stop offset="0" stop-color="#fbe3f1"/>
        <stop offset="0.35" stop-color="#efe6f7"/>
        <stop offset="0.8" stop-color="#ffffff"/>
      </linearGradient>
      <linearGradient id="edge" x1="0" y1="0" x2="1" y2="0">
        <stop offset="0" stop-color="#ec1a8c"/>
        <stop offset="1" stop-color="#9b45c9"/>
      </linearGradient>
    </defs>
    <path d="M0 765 C120 680 230 650 330 650 C500 650 600 800 700 792 C820 782 900 600 960 560 C1040 480 1120 430 1200 435 L1200 1650 L0 1650 Z" fill="url(#softWave)"/>
    <path d="M0 1835 C150 1745 220 1625 330 1615 C500 1605 700 1775 900 1848 C1030 1880 1140 1790 1200 1685 L1200 2162 L0 2162 Z" fill="url(#edge)"/>
    <path d="M0 1855 C150 1760 220 1640 330 1632 C500 1625 700 1790 900 1860 C1050 1885 1150 1780 1200 1690 L1200 2162 L0 2162 Z" fill="#111827"/>
  </svg>

  <header class="site-header">
    <div class="brand"><span class="brand-dot"></span>tanu-werk.de</div>
    <nav class="main-nav">
      <span class="active">Lösungen</span>
      <span>Unternehmen</span>
      <span>Services</span>
      <span>Karriere</span>
      <span class="btn-contact">KONTAKT</span>
    </nav>
  </header>

  <section class="hero">
    <h1>Bieten Sie Ihren Mietern, Mitarbeitern, Kunden, Gästen noch mehr Komfort</h1>
    <p class="lead">Wir beraten, planen und setzen um, die Lösung die Ihr Unternehmen, Wohnpark, Tourismuseinrichtung noch attraktiver macht</p>
    <p class="lead">Ob Kaufen oder Mieten, wir haben DIE Lösung für SIE!</p>
    <p class="note">tanu-werk richtet sich mit seinem Angebot für Gewerbetreibende speziell&nbsp; an:</p>
    <ul class="checks">
      <li>Haus- und Immobilienverwaltungen</li>
      <li>Dienstleistungs- und Handelsunternehmen</li>
      <li>Hotel und Beherbergungsbetriebe</li>
      <li>Parkraum- und Parkhausbetreiber</li>
      <li>Tourismus, Sport- und Freizeiteinrichtungen</li>
    </ul>
  </section>

  <div class="deco-ring" aria-hidden="true"></div>
  <div class="photo photo-socket" role="img" aria-label="Nahaufnahme einer Ladebuchse an einem Elektroauto"></div>

  <div class="photo photo-charging" role="img" aria-label="Hand steckt einen Ladestecker in ein silbernes Elektroauto"></div>

  <section class="service">
    <h2>Laden als Service Dienstleistung</h2>
    <p class="intro">Wenn Sie keine zusätzlichen Kosten und Aufwand mit der Errichtung von Ladepunkten möchten, dann ist unser Modell ‚Laden als Service Dienstleistung“ genau das richtige für SIE.</p>
    <ul class="checks">
      <li>Wir prüfen die örtlichen Gegebenheiten und erstellen eine Machbarkeitsstudie, die wir auf Wunsch auch vor Ihren Eigentümern, Entscheidern oder Geschäftsführung vorstellen.</li>
      <li>Wir übernehmen die notwendigen Genehmigungsverfahren und suchen nach den geeignetsten Förderungsmöglichkeiten</li>
      <li>Wir bieten Ihnen eine Auswahl an smarten Normal- oder Schnell­lademöglichkeiten</li>
      <li>Wir koordinieren die Planung mit allen Gewerken und kümmern uns um die fach- und normengerechte Installation</li>
      <li>Wir stellen die Inbetriebnahme sicher und integrieren die Lösung in Ihre bestehende Infrastruktur, bzw. richten für Mieter, Mitarbeiter, Kunden entsprechende Nutzerkonten ein</li>
      <li>Wir unterstützen Sie bei der Lade-Abrechnung ODER übernehmen diese direkt mit Ihren Nutzern</li>
      <li>Wir sorgen uns um die notwendige Wartung und stehen Ihnen für Reparaturen jederzeit zur Verfügung</li>
      <li>Wir helfen Ihren Nutzern wenn es einmal nicht so funktioniert wie wir es uns wünschen</li>
    </ul>
  </section>

  <footer class="site-footer">
    <div class="brand"><span class="brand-dot"></span>tanu-werk.de</div>
    <nav class="footer-links">
      <span>AGB</span><span>Datenschutzerklärung</span><span>Impressum</span><span>Kontakt</span><span>Karriere</span><span>FAQs</span>
    </nav>
    <div class="socials">
      <span class="social" aria-label="Soziales Netzwerk 1"><span></span></span>
      <span class="social" aria-label="Videokanal"><span></span></span>
      <span class="social" aria-label="Fotokanal"><span></span></span>
    </div>
  </footer>
  <div class="footer-rule"></div>
  <p class="copyright">©tanu-werk GmbH</p>
  <div class="to-top" aria-label="Nach oben"></div>
</body>
</html>
```